RW Framewell Inc Business cards

We need business cards using our existing logo but slightly modified. Right now the logo says RW Loadbearing Masonry. We want to keep the RW part of the design, but replace the Structural Concrete portion with "FRAMEWELL". Please see the attached file.
Ideally this would be a blank template so we can add Different Names, titles, and phone numbers later.
On the one side we want only the logo and on the other side the detail. I'm attaching an example for you to see.
Please reach out with any other questions. Our address and other details will be given out once we find a design we like.

Target Market(s)

Construction Industry

```html
<!DOCTYPE html>
<html lang="en">
<head>
<meta charset="utf-8">
<title>RW Framewell Inc – Business Cards</title>
<link href="https://fonts.googleapis.com/css2?family=Open+Sans:wght@400;600;700&display=swap" rel="stylesheet">
<style>
  :root {
    --backdrop: #4a423d;
    --card-dark: #2f3033;
    --card-dark-mark: #3a3b3f;
    --card-light: #ffffff;
    --brand-blue: #1f78c8;
    --ink-grey: #6b6e72;
    --edge-blue: #1b6fbf;
  }
  * { box-sizing: border-box; margin: 0; padding: 0; }
  html, body {
    width: 1200px; height: 795px; overflow: hidden;
    background: var(--backdrop);
    font-family: "Open Sans", Arial, sans-serif;
  }
  .sheet {
    width: 1200px; height: 795px;
    display: flex; align-items: center; justify-content: center; gap: 48px;
  }
  .card {
    width: 520px; height: 297px; position: relative;
    border-radius: 3px;
    box-shadow: 0 10px 24px rgba(0,0,0,.35);
  }
  .card--back {
    background: var(--card-dark);
    border-bottom: 5px solid var(--edge-blue);
    display: flex; align-items: center; justify-content: center;
  }
  .card--front {
    background: var(--card-light);
    border-bottom: 3px solid var(--edge-blue);
    display: flex; align-items: center; padding: 0 30px 0 36px;
  }
  .wordmark {
    display: flex; flex-direction: column; align-items: flex-start;
    font-weight: 700; line-height: 1;
  }
  .wordmark__initials { font-size: 72px; letter-spacing: 2px; }
  .wordmark__name { font-size: 19px; letter-spacing: 7px; margin-top: 8px; }
  .card--back .wordmark { color: var(--card-dark-mark); }
  .card--back .wordmark__initials { font-size: 96px; }
  .card--back .wordmark__name { font-size: 24px; letter-spacing: 9px; }
  .card--front .wordmark { color: var(--brand-blue); width: 220px; }
  .divider {
    width: 2px; height: 150px; background: var(--brand-blue);
    margin: 0 22px 0 12px;
  }
  .details { color: var(--ink-grey); font-size: 13px; line-height: 1.35; }
  .details__name {
    color: var(--brand-blue); font-weight: 700; font-size: 19px;
    text-transform: uppercase; line-height: 1.1;
  }
  .details__title { font-size: 13px; margin-bottom: 8px; }
  .details__address { margin-bottom: 6px; }
  .contact { list-style: none; }
  .contact li { display: flex; align-items: center; gap: 7px; }
  .contact svg { width: 11px; height: 11px; flex: none; fill: var(--brand-blue); }
</style>
</head>
<body>
<main class="sheet">
  <section class="card card--back" aria-label="Card back">
    <div class="wordmark">
      <span class="wordmark__initials">RW</span>
      <span class="wordmark__name">FRAMEWELL</span>
    </div>
  </section>

  <section class="card card--front" aria-label="Card front">
    <div class="wordmark">
      <span class="wordmark__initials">RW</span>
      <span class="wordmark__name">FRAMEWELL</span>
    </div>
    <div class="divider"></div>
    <div class="details">
      <p class="details__name">Dana Hollis</p>
      <p class="details__title">President</p>
      <p class="details__address">48 Cedar Mill Road<br>Brookvale NY 12345</p>
      <ul class="contact">
        <li><svg viewBox="0 0 24 24" aria-hidden="true"><path d="M6.6 10.8a15 15 0 0 0 6.6 6.6l2.2-2.2a1 1 0 0 1 1-.25 11.4 11.4 0 0 0 3.6.57 1 1 0 0 1 1 1V20a1 1 0 0 1-1 1A17 17 0 0 1 3 4a1 1 0 0 1 1-1h3.5a1 1 0 0 1 1 1c0 1.25.2 2.45.57 3.6a1 1 0 0 1-.25 1z"/></svg>555-014-2290</li>
        <li><svg viewBox="0 0 24 24" aria-hidden="true"><path d="M7 1h10a2 2 0 0 1 2 2v18a2 2 0 0 1-2 2H7a2 2 0 0 1-2-2V3a2 2 0 0 1 2-2zm0 3v14h10V4zm5 15.5a1 1 0 1 0 0 2 1 1 0 0 0 0-2z"/></svg>555-014-2291</li>
        <li><svg viewBox="0 0 24 24" aria-hidden="true"><path d="M2 5h20v14H2zm2 2v.5l8 5 8-5V7zm0 3v7h16v-7l-8 5z"/></svg>hello@framewellmail.com</li>
        <li><svg viewBox="0 0 24 24" aria-hidden="true"><path d="M12 2a10 10 0 1 0 0 20 10 10 0 0 0 0-20zm0 2c.9 0 2.2 2 2.7 5H9.3C9.8 6 11.1 4 12 4zM4.3 11h3a16 16 0 0 0 0 2h-3a8 8 0 0 1 0-2zm5 0h5.4a14 14 0 0 1 0 2H9.3a14 14 0 0 1 0-2zm7.4 0h3a8 8 0 0 1 0 2h-3a16 16 0 0 0 0-2zM9.3 15h5.4c-.5 3-1.8 5-2.7 5s-2.2-2-2.7-5z"/></svg>www.framewellsite.com</li>
      </ul>
    </div>
  </section>
</main>
</body>
</html>
```